SkyvornQ Business Cards and Stationary Design

Need a design for our business cards and stationary. I want to carry on the theme of the logo. I want the business cards to have a design on the back. I would like the business cards and the stationary to carry the same theme, design scheme, and branding

Target Market(s)

Airlines and Maintenance Facilities

Industry/Entity Type

Aviation

Contact Information for Business Card

Name
Position Title
Address: 4827 Trellis Hollow Road, Fort Pierce, Florida, 34951
Office Number
Mobile Number
Email
Website

Font styles to use
Serif
Sans Serif

Colors

Designer to choose colors to be used in the design.

```html
<!DOCTYPE html>
<html lang="en">
<head>
<meta charset="utf-8">
<title>SkyvornQ Business Card</title>
<link rel="stylesheet" href="https://fonts.googleapis.com/css2?family=Work+Sans:wght@400;500;600&display=swap">
<style>
  :root {
    --backdrop: #1c1c1e;
    --card: #262628;
    --card-edge: #2e2e31;
    --ink: #f2f2f2;
    --accent: #1f9be0;
    --accent-deep: #1a5fb4;
    --silver-light: #e4e4e6;
    --silver-mid: #9a9a9e;
    --silver-dark: #3a3a3d;
  }
  * { margin: 0; padding: 0; box-sizing: border-box; }
  html, body {
    width: 1200px; height: 900px; overflow: hidden;
    background: var(--backdrop);
    font-family: "Work Sans", Arial, sans-serif;
    color: var(--ink);
  }
  .canvas { position: relative; width: 1200px; height: 900px; }
  .card {
    position: absolute;
    width: 660px; height: 375px;
    background: var(--card);
    border: 1px solid var(--card-edge);
    box-shadow: 0 18px 40px rgba(0,0,0,.55);
    overflow: hidden;
  }
  .card-front { left: 340px; top: 50px; }
  .card-back  { left: 200px; top: 470px; }

  .front-brand {
    position: absolute; inset: 0;
    display: flex; align-items: center; justify-content: center; gap: 18px;
  }
  .brand-dot {
    width: 22px; height: 22px; border-radius: 50%;
    background: var(--accent-deep);
  }
  .brand-name {
    font-weight: 600; font-size: 46px; letter-spacing: 8px;
    text-transform: uppercase; color: var(--silver-light);
  }

  .back-decoration {
    position: absolute; left: 300px; top: 0; width: 360px; height: 375px;
    background: linear-gradient(200deg, transparent 0%, var(--silver-dark) 35%, var(--silver-mid) 70%, var(--silver-light) 100%);
    clip-path: polygon(18% 0, 55% 0, 100% 55%, 100% 100%, 25% 100%, 60% 62%);
    opacity: .9;
  }
  .back-brand {
    position: absolute; right: 34px; top: 34px;
    font-weight: 600; font-size: 26px; letter-spacing: 5px;
    text-transform: uppercase; color: var(--silver-light);
  }
  .contact { position: absolute; left: 60px; top: 110px; }
  .person-name {
    font-weight: 500; font-size: 28px; letter-spacing: 2px;
    text-transform: uppercase; color: var(--accent);
  }
  .person-title { font-size: 15px; margin-top: 2px; }
  .address { font-size: 17px; line-height: 1.35; margin-top: 22px; }
  .lines { list-style: none; margin-top: 18px; font-size: 17px; line-height: 1.45; }
  .lines li { display: flex; align-items: center; gap: 10px; }
  .lines svg { width: 13px; height: 13px; fill: none; stroke: var(--accent); stroke-width: 1.6; }
  .lines .highlight { color: var(--accent); font-weight: 500; }
</style>
</head>
<body>
<div class="canvas">
  <section class="card card-front">
    <div class="front-brand">
      <span class="brand-dot"></span>
      <span class="brand-name">SkyvornQ</span>
    </div>
  </section>

  <section class="card card-back">
    <div class="back-decoration" role="img" aria-label="Large silver brand mark decoration"></div>
    <div class="back-brand">SkyvornQ</div>
    <div class="contact">
      <h1 class="person-name">Dorian Kell</h1>
      <p class="person-title">Director</p>
      <p class="address">4827 Trellis Hollow Road,<br>Fort Pierce, Florida, 34951</p>
      <ul class="lines">
        <li>
          <svg viewBox="0 0 16 16"><path d="M4 1.5l2.5 3-1.5 1.5a9 9 0 0 0 5 5l1.5-1.5 3 2.5-1.5 2.5C7 14 2 9 1.5 3z"/></svg>
          555-210-3388
        </li>
        <li>
          <svg viewBox="0 0 16 16"><rect x="1.5" y="3.5" width="13" height="9"/><path d="M1.5 3.5l6.5 5 6.5-5"/></svg>
          info@skyvornq.com
        </li>
        <li>
          <svg viewBox="0 0 16 16"><circle cx="8" cy="8" r="6.5"/><path d="M1.5 8h13M8 1.5c-3 3.5-3 9.5 0 13M8 1.5c3 3.5 3 9.5 0 13"/></svg>
          <span>www.<span class="highlight">skyvornq</span>.com</span>
        </li>
      </ul>
    </div>
  </section>
</div>
</body>
</html>
```